VOMRA Pty Ltd Business Card

Looking for a simple yet eye-catching double-sided business card design using my company logo on one side and contact details on the other.

Target Market(s)

Government

Industry/Entity Type

Communication Systems Engineering

Contact Information for Business Card

VOMRA Pty Ltd

Requirements
Nice to have
• Would be great to have a QR code so details can be scanned into contacts

```html
<!DOCTYPE html>
<html lang="en">
<head>
<meta charset="utf-8">
<title>VOMRA Pty Ltd Business Card</title>
<link href="https://fonts.googleapis.com/css2?family=Open+Sans:wght@400;700;800&display=swap" rel="stylesheet">
<style>
  :root {
    --stage: #2c3034;
    --slate: #343b42;
    --paper: #ffffff;
    --paper-grey: #e9e9ea;
    --ink-light: #f2f3f4;
    --ink-dark: #111316;
  }
  * { margin: 0; padding: 0; box-sizing: border-box; }
  html, body {
    width: 1200px; height: 780px; overflow: hidden;
    background: var(--stage);
    font-family: "Open Sans", Arial, sans-serif;
  }
  .canvas {
    position: relative; width: 1200px; height: 780px;
    display: flex; align-items: center; justify-content: center; gap: 48px;
  }
  .card {
    position: relative; width: 520px; height: 297px; overflow: hidden;
    box-shadow: 0 14px 34px rgba(0,0,0,.45);
  }
  /* Front side */
  .card-front { background: var(--paper); display: flex; align-items: center; justify-content: center; }
  .brand { display: flex; align-items: center; gap: 14px; color: var(--slate); }
  .brand-dot { border-radius: 50%; background: var(--slate); }
  .brand-name { font-weight: 800; letter-spacing: .06em; line-height: 1; }
  .card-front .brand-dot { width: 46px; height: 46px; }
  .card-front .brand-name { font-size: 64px; }

  /* Back side */
  .card-back { background: var(--paper-grey); }
  .card-back .brand { position: absolute; left: 34px; top: 40px; gap: 10px; }
  .card-back .brand-dot { width: 26px; height: 26px; }
  .card-back .brand-name { font-size: 36px; }

  .holder { position: absolute; right: 36px; top: 122px; text-align: right; }
  .holder-name { font-size: 25px; font-weight: 700; color: var(--ink-dark); line-height: 1.1; }
  .holder-role { font-size: 14px; color: var(--ink-dark); margin-top: 2px; }
  .edge-tab { position: absolute; right: 0; top: 132px; width: 16px; height: 54px; background: var(--slate); }

  .contact-band {
    position: absolute; left: 0; bottom: 0; width: 360px; height: 138px;
    background: var(--slate); color: var(--ink-light);
    padding: 16px 24px; font-size: 11.5px; line-height: 1.55;
  }
  .contact-address { margin-bottom: 4px; }
  .contact-row { display: flex; align-items: center; gap: 7px; }
  .contact-row svg { width: 11px; height: 11px; flex: none; fill: var(--ink-light); }
</style>
</head>
<body>
<main class="canvas">
  <section class="card card-front" aria-label="Card front">
    <div class="brand">
      <span class="brand-dot"></span>
      <span class="brand-name">VOMRA</span>
    </div>
  </section>

  <section class="card card-back" aria-label="Card back">
    <div class="brand">
      <span class="brand-dot"></span>
      <span class="brand-name">VOMRA</span>
    </div>

    <div class="holder">
      <p class="holder-name">Jordan Mercer</p>
      <p class="holder-role">Co-Founder</p>
    </div>
    <div class="edge-tab"></div>

    <div class="contact-band">
      <p class="contact-address">14-16 Harlow Lane Redfern<br>NSW 2016 Australia</p>
      <p class="contact-row">
        <svg viewBox="0 0 24 24" aria-hidden="true"><path d="M6.6 10.8a15 15 0 0 0 6.6 6.6l2.2-2.2c.3-.3.7-.4 1-.2 1.1.4 2.3.6 3.6.6.6 0 1 .4 1 1V20c0 .6-.4 1-1 1A17 17 0 0 1 3 4c0-.6.4-1 1-1h3.5c.6 0 1 .4 1 1 0 1.3.2 2.5.6 3.6.1.3 0 .7-.2 1z"/></svg>
        (555) 012-4837
      </p>
      <p class="contact-row">
        <svg viewBox="0 0 24 24" aria-hidden="true"><circle cx="12" cy="12" r="10"/></svg>
        www.vomra.com.au
      </p>
      <p class="contact-row">
        <svg viewBox="0 0 24 24" aria-hidden="true"><path d="M2 5h20v14H2z M2 5l10 8 10-8" /></svg>
        admin@vomra.com.au
      </p>
    </div>
  </section>
</main>
</body>
</html>
```